KLORA product web page

We need a new web design for our KLORA product page. You can find more information about the project on the current web site - www.klora.example

What we need from a new design (uncoded):
- landing pages + template
- all information on one page
- the design should be focused on the product - light bulb + app
- web site should be with some dynamics like a background with parallax effect in the current version
- fonts should be chosen
- a number of illustrations should be designed

Here is schema for a new design: https://files.examplehost.net/d/draw-7QpX2mLk9RtYv4Hs/edit

Here is a document with all texts for a new design: https://files.examplehost.net/d/doc-3WnZ8bJf5KcUe1Ga/edit

Illustrations to use:
v1 - https://files.examplehost.net/f/fold-A1kT9pQw2ZxR
v2 - https://files.examplehost.net/f/fold-B7mH4sLv6YcN

MobiOS screens: https://files.examplehost.net/f/fold-C3rJ8dKe1WuP

KLORA logo: https://files.examplehost.net/f/fold-D5nF2gTb9XoM
Updates

I forgot to add the definition text "KLORA - is.." to the document with texts. Sorry, my mistake.

Target Market(s)

25-45 year old adults who are interested in "smart" devices for their health.

Industry/Entity Type

Brintel

Colors

Designer to choose colors to be used in the design.

Requirements
Must have
• - landing pages + template
- fonts should be chosen

```html
<!DOCTYPE html>
<html lang="en">
<head>
<meta charset="utf-8">
<title>KLORA — smart LED bulb</title>
<link rel="stylesheet" href="https://fonts.googleapis.com/css2?family=Open+Sans:wght@300;400;600;700&display=swap">
<style>
:root{
  --brand-blue:#1b8fd2;
  --deep-blue:#1479b5;
  --purple:#6b2d90;
  --olive:#93a514;
  --yellow:#f5b324;
  --ink:#2b2b2b;
  --dark:#1e1e1f;
  --mist:#ececec;
  --white:#ffffff;
  --muted:#cfcfcf;
}
*{box-sizing:border-box;margin:0;padding:0}
html,body{width:1200px;height:5143px;overflow:hidden}
body{font-family:"Open Sans",Arial,sans-serif;color:var(--white);background:var(--white);position:relative}
section,header,footer{position:absolute;left:0;width:1200px;overflow:hidden}
.abs{position:absolute}
.btn{position:absolute;display:inline-block;font-size:15px;font-weight:600;padding:0 26px;height:44px;line-height:44px;border-radius:2px;color:var(--white)}
.btn-dark{background:#2a2a2b}
.btn-blue{background:var(--brand-blue)}
.btn-yellow{background:var(--yellow);color:#2a2a2a}
.btn-olive{background:var(--olive)}
.dots{position:absolute;right:42px;display:flex;flex-direction:column;gap:12px}
.dots span{width:12px;height:12px;border-radius:50%;border:2px solid var(--white);display:block}
.dots span.on{background:var(--white)}
.dots.grey span{border-color:#8a8a8a}
.dots.grey span.on{background:#8a8a8a}
.photo{position:absolute}
.h2{font-weight:300;font-size:40px}
.copy{font-size:14px;line-height:1.7}
.copy p+p{margin-top:16px}
.ticks{list-style:none;font-size:14px;line-height:1.6}
.ticks li{position:relative;padding-left:30px;margin-bottom:14px}
.ticks li svg{position:absolute;left:0;top:3px}

/* header */
.site-header{top:0;height:92px;background:var(--white)}
.logo{position:absolute;left:84px;top:18px;font-weight:700;font-size:44px;letter-spacing:3px;color:var(--brand-blue)}
.nav{position:absolute;right:84px;top:30px;display:flex;gap:30px;align-items:center;font-size:14px;font-weight:600;color:var(--brand-blue)}
.nav .pre{background:#333;color:var(--white);padding:6px 14px;border-radius:2px}

/* hero */
.hero{top:92px;height:611px;background:#141414}
.hero-title{left:72px;top:100px;font-size:46px;font-weight:600}
.hero-text{left:72px;top:170px;width:560px;font-size:22px;line-height:1.5}
.arrow-side{position:absolute;top:250px}
.chev{position:absolute;width:72px;height:72px;border:3px solid var(--white);border-radius:50%}

/* purple band */
.intro{top:703px;height:103px;background:var(--purple)}
.intro p{position:absolute;left:72px;top:22px;width:800px;font-size:19px;line-height:1.5}

/* what we do */
.what{top:806px;height:676px;background:var(--brand-blue);text-align:center}
.what .h2{position:absolute;left:0;width:1200px;top:100px;font-size:48px}
.what .sub{position:absolute;left:0;width:1200px;top:170px;font-size:14px}
.card{position:absolute;top:213px;width:280px;height:398px;background:var(--white);color:var(--ink);border-radius:3px;padding:22px}
.card .icon{width:236px;height:190px;background:var(--brand-blue);display:flex;align-items:center;justify-content:center}
.card h3{font-size:22px;font-weight:400;margin:14px 0 8px}
.card p{font-size:12px;line-height:1.55;color:#555}

/* feature blocks */
.app{top:1482px;height:662px;background:#232324}
.color{top:2144px;height:514px;background:var(--olive)}
.health{top:2658px;height:635px;background:#1b1b1c}
.specs{top:3293px;height:593px;background:var(--mist);color:var(--ink)}
.design{top:3886px;height:539px;background:#3a2216}
.order{top:4425px;height:651px;background:var(--brand-blue)}
.order input{position:absolute;left:86px;top:257px;width:480px;height:66px;border:none;background:var(--white);font:18px "Open Sans",Arial,sans-serif;padding:0 22px;color:#666}
.order .send{position:absolute;left:566px;top:257px;width:66px;height:66px;background:var(--deep-blue);display:flex;align-items:center;justify-content:center}

/* footer */
.site-footer{top:5076px;height:67px;background:var(--white);color:#555;font-size:13px}
.site-footer .legal{position:absolute;left:86px;top:24px}
.social{position:absolute;right:86px;top:14px;display:flex;align-items:center;gap:10px}
.social i{width:36px;height:36px;border-radius:50%;background:#555;display:block}
</style>
</head>
<body>

<header class="site-header">
  <div class="logo">KLORA</div>
  <nav class="nav"><span class="pre">PRE-ORDER</span><span>BLOG</span><span>CONTACTS</span><span>RU</span></nav>
</header>

<section class="hero">
  <div class="photo" role="img" aria-label="Glowing KLORA LED bulb lighting a dark room" style="left:0;top:0;width:1200px;height:611px;background:radial-gradient(circle at 980px 230px,#fff7e6 0,#e8d7b8 60px,#7a6a55 200px,#2b2621 380px,#141414 620px)"></div>
  <h1 class="abs hero-title">KLORA</h1>
  <p class="abs hero-text">KLORA - smart LED bulb that understands your needs: play with millions of colors and control your lighting with a mobile device</p>
  <a class="btn btn-blue" style="left:72px;top:400px">Pre-order</a>
  <a class="btn btn-yellow" style="left:252px;top:400px">Discover more</a>
  <svg class="arrow-side" style="left:26px" width="16" height="28" viewBox="0 0 16 28"><path d="M14 2 3 14l11 12" fill="none" stroke="#fff" stroke-width="3"/></svg>
  <svg class="arrow-side" style="right:26px" width="16" height="28" viewBox="0 0 16 28"><path d="M2 2l11 12L2 26" fill="none" stroke="#fff" stroke-width="3"/></svg>
  <div class="chev" style="left:564px;top:470px"><svg width="66" height="66" viewBox="0 0 66 66"><path d="M21 27l12 12 12-12" fill="none" stroke="#fff" stroke-width="3"/></svg></div>
</section>

<section class="intro">
  <p>KLORA is the right lighting designed especialy for your health and comfort: a smart true color bluetooth enabled LED light bulb.</p>
  <a class="btn btn-dark" style="left:910px;top:30px;width:178px;text-align:center">Read more</a>
</section>

<section class="what">
  <h2 class="h2">What We do</h2>
  <p class="sub">To preset moods provide positive impact on your health.</p>
  <article class="card" style="left:103px">
    <div class="icon"><svg width="80" height="80" viewBox="0 0 80 80" fill="#fff"><rect x="4" y="4" width="18" height="18" rx="3"/><rect x="31" y="4" width="18" height="18" rx="3"/><rect x="58" y="4" width="18" height="18" rx="3"/><rect x="4" y="31" width="18" height="18" rx="3"/><rect x="31" y="31" width="18" height="18" rx="3"/><rect x="58" y="31" width="18" height="18" rx="3"/><rect x="4" y="58" width="18" height="18" rx="3"/><rect x="31" y="58" width="18" height="18" rx="3"/><rect x="58" y="58" width="18" height="18" rx="3"/></svg></div>
    <h3>KLORA APP</h3>
    <p>KLORA Application allows you to control each lightbulb at home. Manage your lighting by creating functional groups and adding lightbulbs. Correctly matched lighting will help you work more productively and relax to the utmost.</p>
  </article>
  <article class="card" style="left:463px">
    <div class="icon"><svg width="90" height="90" viewBox="0 0 90 90"><path d="M45 8C22 8 8 24 8 44c0 20 16 36 34 36 8 0 9-6 5-11-4-5 0-11 7-11h10c10 0 18-7 18-18C82 22 66 8 45 8z" fill="none" stroke="#fff" stroke-width="5"/><circle cx="28" cy="36" r="6" fill="#fff"/><circle cx="44" cy="24" r="6" fill="#fff"/><circle cx="62" cy="30" r="6" fill="#fff"/><circle cx="24" cy="56" r="6" fill="#fff"/></svg></div>
    <h3>KLORA COLOR</h3>
    <p>Experiment with millions of colors! Pick any color from the screen of your mobile device and transform ordinary lighting into the right shade of a calm seaside evening or a sunny meadow and refresh your best memories.</p>
  </article>
  <article class="card" style="left:833px">
    <div class="icon"><svg width="60" height="96" viewBox="0 0 60 96" fill="none" stroke="#fff" stroke-width="5"><path d="M10 8h40M8 22l44-6M8 36l44-6M8 50l44-6M14 60h32l-4 18H18z"/><path d="M22 86h16"/></svg></div>
    <h3>KLORA</h3>
    <p>KLORA lightbulb is a 60W incandescent equivalent that transforms your visual environment. E27 socket: no need to change anything. Easy way to home automation at hand. And yes, you can still use those switches.</p>
  </article>
  <div class="dots" style="top:282px"><span class="on"></span><span></span><span></span><span></span><span></span><span></span></div>
</section>

<section class="app">
  <div class="photo" role="img" aria-label="KLORA bulb glowing beside a phone showing the KLORA app" style="left:100px;top:130px;width:360px;height:420px;background:radial-gradient(circle at 110px 90px,#ffffff 0,#d8d8d8 60px,#3a3a3b 180px,#232324 300px)"></div>
  <h2 class="abs h2" style="left:568px;top:150px;font-size:36px">✓ KLORA App</h2>
  <div class="abs copy" style="left:568px;top:230px;width:520px">
    <p>KLORA Application allows you to control each lightbulb at home. Manage your lighting by creating functional groups and adding lightbulbs. Correctly matched lighting will help you work more productively and relax to the utmost.</p>
    <p>Create light scenes and adapt them to your needs. KLORA App memorizes your favorite moods, so that you can use your settings anytime.</p>
    <p>Play with million colors and adjust the brightness of your home lighting. KLORA works on MobiOS 6+ and Robodroid 4+.</p>
  </div>
  <a class="btn btn-dark" style="left:568px;top:460px">Discover more</a>
  <div class="dots" style="top:200px"><span></span><span class="on"></span><span></span><span></span><span></span><span></span></div>
</section>

<section class="color">
  <h2 class="abs h2" style="left:86px;top:100px;font-size:36px">✓ KLORA and color</h2>
  <div class="abs copy" style="left:86px;top:170px;width:560px;font-size:13px">
    <p>Experiment with millions of colors! Pick any color from the screen of your mobile device and enjoy the ambience. LED lightbulb KLORA can transform conventional lighting into the right lights of seaside or spring in the rich summer hues of meadows. Enliven your fantasies or raise your best memories in one click. Change the atmosphere around you by changing colors. You will literally see the world in a new light.</p>
  </div>
  <a class="btn btn-dark" style="left:86px;top:332px">Discover more</a>
  <div class="photo" role="img" aria-label="Three KLORA bulbs glowing cyan, red and yellow" style="left:760px;top:80px;width:380px;height:380px;background:radial-gradient(circle at 90px 130px,#5fe4f0 0,rgba(95,228,240,.3) 70px,transparent 120px),radial-gradient(circle at 170px 200px,#ff3b3b 0,rgba(255,59,59,.3) 50px,transparent 90px),radial-gradient(circle at 280px 80px,#ffe35a 0,rgba(255,227,90,.35) 80px,transparent 150px)"></div>
  <div class="dots" style="top:110px"><span></span><span></span><span class="on"></span><span></span><span></span><span></span></div>
</section>

<section class="health">
  <div class="photo" role="img" aria-label="KLORA bulb hanging by a window at dusk" style="left:0;top:0;width:520px;height:635px;background:radial-gradient(circle at 270px 330px,#ffffff 0,#d9e2e6 70px,#4a5156 220px,#1b1b1c 420px)"></div>
  <h2 class="abs h2" style="left:555px;top:128px">KLORA and health</h2>
  <p class="abs" style="left:555px;top:190px;font-size:16px;color:var(--muted)">Lorem Ipsum Dolor Sit amet and typesetting industry and lopum send.</p>
  <ul class="abs ticks" style="left:555px;top:258px;width:560px">
    <li><svg width="16" height="14"><path d="M1 7l5 5 9-11" fill="none" stroke="#fff" stroke-width="3"/></svg>The right light for your vision: optimized color rendering and color temperature</li>
    <li><svg width="16" height="14"><path d="M1 7l5 5 9-11" fill="none" stroke="#fff" stroke-width="3"/></svg>KLORA creates the appropriate lighting for concentration and relaxation considering your emotional and physical state</li>
    <li><svg width="16" height="14"><path d="M1 7l5 5 9-11" fill="none" stroke="#fff" stroke-width="3"/></svg>Lighting for healthy sleep and natural awakening: set your alarm clock to light up gradually, stay in harmony with your biological rhythms</li>
  </ul>
  <a class="btn btn-olive" style="left:505px;top:434px;width:184px;text-align:center">Read more</a>
  <div class="dots" style="top:200px"><span></span><span></span><span></span><span class="on"></span><span></span><span></span></div>
</section>

<section class="specs">
  <h2 class="abs h2" style="left:100px;top:90px;font-size:38px">KLORA technical specifications</h2>
  <ul class="abs ticks" style="left:100px;top:170px;width:620px;font-size:13px">
    <li><svg width="16" height="14"><path d="M1 7l5 5 9-11" fill="none" stroke="#f5b324" stroke-width="3"/></svg>KLORA lightbulb is a 60W incandescent equivalent that transforms your visual environment.</li>
    <li><svg width="16" height="14"><path d="M1 7l5 5 9-11" fill="none" stroke="#f5b324" stroke-width="3"/></svg>E27 socket: no need to change anything. Easy way to home automation at hand. And yes, you can still use those switches.</li>
    <li><svg width="16" height="14"><path d="M1 7l5 5 9-11" fill="none" stroke="#f5b324" stroke-width="3"/></svg>12.5W (110 - 230V 50Hz), 1000lm+: energy-efficient LED lightbulb KLORA shines brighter than others and saves energy.</li>
    <li><svg width="16" height="14"><path d="M1 7l5 5 9-11" fill="none" stroke="#f5b324" stroke-width="3"/></svg>2700-5500K: You are not limited in your choice of color temperature. Turn on warm or cool light depending on your activities.</li>
    <li><svg width="16" height="14"><path d="M1 7l5 5 9-11" fill="none" stroke="#f5b324" stroke-width="3"/></svg>Compatibility:</li>
  </ul>
  <a class="btn btn-yellow" style="left:100px;top:450px;width:150px;text-align:center">Read more</a>
  <div class="photo" role="img" aria-label="KLORA bulb above a phone showing the bedroom lighting screen" style="left:780px;top:0;width:380px;height:593px;background:radial-gradient(circle at 210px 40px,#ffffff 0,#dcdcdc 60px,transparent 140px),linear-gradient(180deg,var(--mist) 40%,#c9c9c9 100%)"></div>
  <div class="dots grey" style="top:160px"><span></span><span></span><span></span><span></span><span class="on"></span><span></span></div>
</section>

<section class="design">
  <div class="photo" role="img" aria-label="KLORA bulb on a warm wooden interior background" style="left:0;top:0;width:1200px;height:539px;background:radial-gradient(circle at 170px 250px,#ffffff 0,#e8d8c8 70px,#7a4a30 230px,transparent 420px),linear-gradient(90deg,#5a3423,#3a2216 60%,#2a180f)"></div>
  <h2 class="abs h2" style="left:600px;top:124px;font-size:36px">✓ Lighting Design</h2>
  <div class="abs copy" style="left:600px;top:196px;width:520px;font-size:13px">
    <p>Wireless lightbulbs with Bluetooth and MeshLink help you implement the concept of the smart home. KLORA makes it affordable. Real lighting design at your place couldn't have been simpler.</p>
    <p>Create optimal lighting for each functional area - set the perfect light for your kitchen, living room and nursery. Name individual lightbulbs or groups of them, set your color mood, pick a palette for each room. Stay informed of every smart lightbulb's condition.</p>
  </div>
  <a class="btn btn-yellow" style="left:605px;top:392px">Discover more</a>
  <div class="dots" style="top:150px"><span></span><span></span><span></span><span></span><span></span><span class="on"></span></div>
</section>

<section class="order">
  <h2 class="abs h2" style="left:86px;top:118px;font-size:40px">Get your Klora</h2>
  <p class="abs" style="left:86px;top:190px;font-size:13px;font-weight:700">Enter your e-mail and we will notify you when it's available</p>
  <input type="email" value="E-mail address" aria-label="E-mail address">
  <div class="send"><svg width="26" height="20" viewBox="0 0 26 20"><path d="M1 1h24v18H1zM1 1l12 10L25 1" fill="none" stroke="#fff" stroke-width="2"/></svg></div>
  <p class="abs copy" style="left:86px;top:370px;width:560px;font-size:13px">Wireless lightbulbs with Bluetooth and MeshLink help you implement the concept of the smart home. KLORA makes it affordable. Real lighting design at your place couldn't have been simpler. Create optimal lighting for each functional area - set the perfect light for your kitchen, living room and nursery.</p>
  <div class="photo" role="img" aria-label="KLORA bulb glowing softly" style="left:800px;top:120px;width:360px;height:440px;background:radial-gradient(circle at 160px 150px,#ffffff 0,#d7ecf8 70px,rgba(27,143,210,0) 220px)"></div>
  <div class="chev" style="left:564px;top:540px"><svg width="66" height="66" viewBox="0 0 66 66"><path d="M21 39l12-12 12 12" fill="none" stroke="#fff" stroke-width="3"/></svg></div>
  <div class="dots" style="top:140px"><span></span><span></span><span></span><span></span><span></span><span class="on"></span></div>
</section>

<footer class="site-footer">
  <span class="legal">©Klora Labs Ltd. 2014</span>
  <div class="social"><span style="margin-right:8px">Socialize with us</span><i></i><i></i><i></i><i></i></div>
</footer>

</body>
</html>
```